Business Card Design

New business card design

Target Market(s)

Residential & Commercial Property Managers

Industry/Entity Type

Plumbing Services

Contact Information for Business Card

Name - Rowan Keddle, title - Director, Phone Number - 0431 286 517, email - rowan@tbk-plumbing.com.au, Company ABN - 73 215 904 386,

Font styles to use
Sans Serif

Colors
0054AA
0677BA
7BADD7
CADEEF
E8F1F8

```html
<!DOCTYPE html>
<html lang="en">
<head>
<meta charset="utf-8">
<title>TBK Plumbing Services – Business Card</title>
<link rel="stylesheet" href="https://fonts.googleapis.com/css2?family=Roboto:wght@400;700&display=swap">
<style>
  :root {
    --page: #ededed;
    --card-white: #ffffff;
    --ink-dark: #1f232b;
    --ink-text: #4a4d52;
    --ink-muted: #7a7d82;
    --accent-blue: #1aa3e0;
    --emboss: #343b47;
    --divider: #b9bcc0;
  }
  * { margin: 0; padding: 0; box-sizing: border-box; }
  html, body {
    width: 1200px; height: 900px; overflow: hidden;
    background: var(--page);
    font-family: "Roboto", Arial, sans-serif;
  }
  .canvas { position: relative; width: 1200px; height: 900px; }

  .card {
    position: absolute; left: 285px;
    width: 630px; height: 360px;
    border-radius: 22px;
    border: 4px solid var(--accent-blue);
    overflow: hidden;
    box-shadow: 0 10px 24px rgba(0,0,0,.18);
  }
  .card--front { top: 60px; background: var(--card-white); }
  .card--back  { top: 480px; background: var(--ink-dark); }

  /* company name: plain set text with one plain circle */
  .company {
    position: absolute;
    display: flex; align-items: center; gap: 14px;
  }
  .company__mark {
    flex: none; width: 22px; height: 22px; border-radius: 50%;
    background: var(--accent-blue);
  }
  .company__name {
    font-weight: 700; font-size: 28px; line-height: 1.15;
    color: var(--ink-dark);
  }
  .card--front .company { left: 40px; top: 118px; width: 235px; }
  .card--back .company {
    left: 0; right: 0; top: 150px; justify-content: center;
  }
  .card--back .company__name { color: var(--emboss); font-size: 36px; }

  .divider {
    position: absolute; left: 290px; top: 92px;
    width: 1px; height: 130px; background: var(--divider);
  }

  .contact { position: absolute; left: 312px; top: 100px; }
  .contact__name {
    color: var(--accent-blue); font-weight: 700; font-size: 27px;
    text-transform: uppercase; letter-spacing: .3px; line-height: 1.1;
  }
  .contact__role { color: var(--ink-muted); font-size: 17px; margin-top: 4px; }
  .contact__line {
    display: flex; align-items: center; gap: 7px;
    color: var(--ink-text); font-size: 17px; margin-top: 10px;
  }
  .contact__line + .contact__line { margin-top: 4px; }
  .contact__icon { width: 14px; height: 14px; flex: none; }

  .abn-band {
    position: absolute; left: 0; top: 272px;
    width: 438px; height: 40px; background: var(--ink-dark);
    display: flex; align-items: center; padding-left: 220px;
    color: #fff; font-size: 17px;
  }
  .abn-band__label { color: var(--accent-blue); margin-right: 6px; }
  .accent-band {
    position: absolute; left: 438px; top: 292px;
    width: 200px; height: 40px; background: var(--accent-blue);
  }
  .accent-dot {
    position: absolute; left: 412px; top: 260px;
    width: 56px; height: 56px; border-radius: 50%;
    background: var(--accent-blue); border: 5px solid var(--card-white);
  }
</style>
</head>
<body>
<main class="canvas">

  <section class="card card--front" aria-label="Business card front">
    <div class="company">
      <span class="company__mark" aria-hidden="true"></span>
      <span class="company__name">TBK Plumbing Services</span>
    </div>
    <div class="divider"></div>
    <div class="contact">
      <p class="contact__name">Rowan Keddle</p>
      <p class="contact__role">Director</p>
      <p class="contact__line">
        <svg class="contact__icon" viewBox="0 0 16 16" aria-hidden="true">
          <path fill="#1aa3e0" d="M3.6 1.2l2.3 2.9-1.4 1.6c.9 2 2.5 3.6 4.5 4.5l1.6-1.4 2.9 2.3-1.3 2.6C7 13.3 2.7 9 1 3z"/>
        </svg>
        0431 286 517
      </p>
      <p class="contact__line">
        <svg class="contact__icon" viewBox="0 0 16 16" aria-hidden="true">
          <rect x="1" y="3" width="14" height="10" rx="1.5" fill="#1aa3e0"/>
          <path d="M2 4.5l6 4.5 6-4.5" fill="none" stroke="#fff" stroke-width="1.4"/>
        </svg>
        rowan@tbk-plumbing.com.au
      </p>
    </div>
    <div class="abn-band"><span class="abn-band__label">ABN:</span>73 215 904 386</div>
    <div class="accent-band"></div>
    <div class="accent-dot"></div>
  </section>

  <section class="card card--back" aria-label="Business card back">
    <div class="company">
      <span class="company__mark" aria-hidden="true"></span>
      <span class="company__name">TBK Plumbing Services</span>
    </div>
  </section>

</main>
</body>
</html>
```